Web Design Project - Shipping Industry

Goals and Objectives
The objective of the new website is to create a more modern look and feel. The site will also allow for a more effective means of communicating with members while providing the public with information and developments in the local, regional and international shipping industry.
Scope
The website will highlight the history of the organisation inclusive of text and photographs. It will take visitors through the years from beginning to present. Information on the history of the shipping industry will also be included.
It will feature current articles on the organisation, its members and stakeholders in the shipping industry. Member information as well as pertinent details regarding the organisation’s subsidiaries will be documented for the website.
Information as it relates to shipping statistics, case studies, laws and regulations, international treaties and trade documents, shipping terms, careers in shipping, job opportunities, training opportunities, information for shippers including port listing and trade lanes will be main features of the content for the website.
The Association’s community involvement, industry calendar events and related links relevant industry members will also be featured.
Target Market
• The General Public;
• Members of the organization;
• Shipping Industry Stakeholders (local, regional and international);
• Tertiary students conducting research.
• Potential employees
• Potential Business Partners
Best Practice Bench Marketing
The following websites are being looked at:
• Korvel Quayworks - http://www.korvelquayworks.example/ (preferred look)
• Tessaly Maritime Association - http://www.tma-freight.example/ (like image transition on main page)
• Drovna - http://www.drovna.example (professional look)
• PLW - http://www.pelworth.example (preferred color: blue in logo)
• Quillo - http://www.quillo.example/electronics/tv-video-audio/ (preferred look for links page: image + short text below + visit site link)
Expected Result
• 3 - 5 pages which must include: [1] main page [2] standard page [3] links page

```html
<!DOCTYPE html>
<html lang="en">
<head>
<meta charset="utf-8">
<title>The Harbourline Shipping Association</title>
<link rel="stylesheet" href="https://fonts.googleapis.com/css2?family=Arimo:wght@400;700&family=Oswald:wght@500&family=Crimson+Text:wght@400&display=swap">
<style>
:root{
  --navy:#03036a;
  --frame:#07078a;
  --blue:#1a8fef;
  --sky:#2cb2f6;
  --ink:#2a2a2a;
  --text:#333;
  --white:#fff;
  --grey:#e5e5e5;
  --link:#1565b8;
  --news-btn:#0a3b8f;
  --footer-link:#3a64c8;
}
*{margin:0;padding:0;box-sizing:border-box}
html,body{width:1200px;height:1000px;overflow:hidden}
body{background:var(--navy);font-family:Arimo,Arial,sans-serif;color:var(--text);position:relative}
a{text-decoration:none;color:inherit}
.brand{position:absolute;left:134px;top:32px;width:320px;height:100px}
.brand-mark{position:absolute;left:112px;top:2px;width:40px;height:40px;border-radius:50%;background:var(--blue)}
.brand-name{position:absolute;left:0;top:72px;font-family:"Crimson Text",Georgia,serif;font-size:20px;color:var(--blue);white-space:nowrap}
.login{position:absolute;left:821px;top:15px;width:231px;height:40px;background:var(--blue);border-radius:3px;color:#16408a;font-size:15px;font-weight:700;text-align:center;line-height:40px}
.search{position:absolute;left:822px;top:64px;width:229px;height:44px;background:var(--white);border-radius:5px}
.search-field{position:absolute;left:7px;top:7px;width:157px;height:30px;background:#f0f0f0;border:1px solid #e2e2e2}
.search-btn{position:absolute;left:157px;top:7px;width:65px;height:30px;background:#2a2a2a;color:#fff;font-size:9px;letter-spacing:.5px;text-align:center;line-height:30px}
.nav{position:absolute;left:478px;top:118px;display:flex;height:34px}
.nav a{color:#fff;font-size:9.5px;letter-spacing:.6px;padding:0 7px;line-height:34px}
.nav a.active{background:linear-gradient(#1aa0f0,#0a6fc8)}
.frame{position:absolute;left:122px;top:152px;width:940px;height:848px;background:var(--frame)}
.panel{position:absolute;left:133px;top:163px;width:919px;height:673px;background:var(--white)}
.slide{position:absolute;left:11px;top:9px;width:619px;height:279px;background:linear-gradient(100deg,#dfe3ea 0%,#c9cfd8 40%,#e8d98a 62%,#3b3f4a 100%);border:1px solid #c8ccd4}
.dots{position:absolute;left:562px;top:299px;display:flex;gap:6px}
.dots span{width:8px;height:8px;border-radius:50%;background:#c8c8c8}
.dots span.on{background:#555}
.welcome{position:absolute;left:14px;top:324px;font-family:Oswald,sans-serif;font-weight:500;font-size:28px;color:var(--ink);letter-spacing:.2px;white-space:nowrap}
.welcome em{font-style:normal;color:var(--blue)}
.intro{position:absolute;left:18px;top:373px;width:616px;font-size:11.2px;line-height:14px;text-align:justify}
.intro p{margin-bottom:13px}
.news-title{position:absolute;left:665px;top:16px;font-family:Oswald,sans-serif;font-weight:500;font-size:28px;color:var(--ink)}
.news{position:absolute;left:650px;top:60px;width:249px;height:474px;background:var(--blue);border-radius:2px;padding:0 8px}
.news-item{height:153px;border-bottom:1px dotted #9fd3ff;padding:12px 5px 0;position:relative}
.news-item:last-child{border-bottom:none}
.news-item h3{font-size:13px;font-weight:700;color:#111;line-height:16px}
.news-thumb{position:absolute;left:5px;top:58px;width:66px;height:66px;background:linear-gradient(#9aa7b5,#c7cdd4);border:3px solid #fff;border-radius:3px}
.news-item p{position:absolute;left:86px;top:62px;width:144px;font-size:10px;line-height:12.5px;color:#fff}
.news-item .more{position:absolute;left:86px;top:127px;background:var(--news-btn);color:#fff;font-size:10px;padding:3px 4px}
.directory{position:absolute;left:12px;top:592px;width:175px;height:39px;background:var(--sky);border-radius:3px;color:#fff;font-family:Oswald,sans-serif;font-size:16px;text-align:center;line-height:39px;letter-spacing:.5px}
.social{position:absolute;top:591px;width:40px;height:40px;border-radius:50%;background:#e2e6ea;border:1px solid #c9d0d6}
.social.gallery{left:202px}
.social.feed{left:248px}
.quick{position:absolute;left:306px;top:553px;width:602px;height:110px;background:var(--grey);border-radius:4px;padding:8px 14px}
.quick h2{font-weight:400;font-size:21px;color:#222}
.quick ul{list-style:none;display:grid;grid-template-columns:151px 146px 141px 130px;row-gap:6px;margin-top:9px}
.quick li{font-size:10.3px;color:var(--link);padding-left:10px;position:relative;line-height:13px;white-space:nowrap}
.quick li::before{content:"";position:absolute;left:0;top:3px;border-left:4px solid #1565b8;border-top:3px solid transparent;border-bottom:3px solid transparent}
.footer-links{position:absolute;left:503px;top:890px;width:141px;list-style:none}
.footer-links li{font-size:10px;color:#fff;height:19px;line-height:19px;border-bottom:1px dotted #3a4ab8;padding-left:12px;position:relative}
.footer-links li::before{content:"";position:absolute;left:0;top:5px;border-left:5px solid #fff;border-top:4px solid transparent;border-bottom:4px solid transparent}
.footer-links li.plain::before{display:none}
.lang{position:absolute;left:794px;top:853px;width:195px}
.lang h4{font-size:15px;font-weight:700;color:#fff;padding-left:32px;position:relative;padding-bottom:6px;border-bottom:1px dotted #8a9ae8}
.lang h4 svg{position:absolute;left:0;top:-3px}
.lang ul{list-style:none;display:grid;grid-template-columns:116px 80px;row-gap:5px;margin-top:10px;padding-left:10px}
.lang li{font-size:10px;color:var(--footer-link);line-height:14px}
.copy{position:absolute;left:148px;top:970px;font-size:10px;color:var(--footer-link)}
</style>
</head>
<body>
<header>
  <a class="brand" href="#"><span class="brand-mark"></span><span class="brand-name">the harbourline shipping association</span></a>
  <a class="login" href="#">Log In / Register</a>
  <form class="search"><span class="search-field"></span><span class="search-btn">SEARCH</span></form>
  <nav class="nav">
    <a class="active" href="#">ABOUT US</a><a href="#">CONTRIBUTE</a><a href="#">SERVICE AND FELLOWSHIP</a><a href="#">STUDENTS AND YOUTH</a><a href="#">MEMBERS</a><a href="#">MEDIA AND NEWS</a>
  </nav>
</header>
<div class="frame"></div>
<main class="panel">
  <div class="slide" role="img" aria-label="Photo of association officials in suits beside a painted mural at a terminal building"></div>
  <div class="dots"><span class="on"></span><span></span><span></span><span></span><span></span></div>
  <h1 class="welcome">WELCOME TO OUR <em>OFFICIAL WEBSITE</em></h1>
  <div class="intro">
    <p>Lorem ipsum dolor sit amet, consectetur adipiscing elit. Sed ullamcorper accumsan leo vel posuere. Sed rhoncus luctus imperdiet. Nulla nec dui nec nisl rutrum luctus et tristique diam. Aliquam molestie pharetra felis, eu consectetur justo iaculis in.</p>
    <p>Mauris varius, orci quis mollis condimentum, magna elit dictum sem, volutpat placerat felis tellus eget orci. Ut quis dolor leo, facilisis vestibulum purus. Aliquam arcu justo, congue non pellentesque vel, cursus vitae nisi. Curabitur sapien libero, eleifend pulvinar posuere at, egestas vel enim. Fusce iaculis tempor faucibus. Maecenas non mauris et neque pellentesque rhoncus non in nulla.</p>
    <p>Aenean dolor nunc, aliquet hendrerit tempor id, adipiscing eu lectus. Donec porttitor, nulla sit amet fermentum rutrum, leo augue bibendum enim, quis aliquet augue eros id felis. Ut eu nibh eget ante elementum consequat.</p>
  </div>
  <h2 class="news-title">NEWS</h2>
  <section class="news">
    <article class="news-item"><h3>Lorem ipsum dolor sit amet, consectetur...</h3><div class="news-thumb" role="img" aria-label="Photo of port workers in safety vests"></div><p>Sed ullamcorper accumsan leo vel posuere. Sed rhoncus luctus imperdiet. Nulla nec dui nec nisl rutrum luctus et tristique diam.</p><a class="more" href="#">READ MORE</a></article>
    <article class="news-item"><h3>Lorem ipsum dolor sit amet, consectetur...</h3><div class="news-thumb" role="img" aria-label="Photo of staff working at a computer"></div><p>Sed ullamcorper accumsan leo vel posuere. Sed rhoncus luctus imperdiet. Nulla nec dui nec nisl rutrum luctus et tristique diam.</p><a class="more" href="#">READ MORE</a></article>
    <article class="news-item"><h3>Lorem ipsum dolor sit amet, consectetur...</h3><div class="news-thumb" role="img" aria-label="Photo of a community health visit"></div><p>Sed ullamcorper accumsan leo vel posuere. Sed rhoncus luctus imperdiet. Nulla nec dui nec nisl rutrum luctus et tristique diam.</p><a class="more" href="#">READ MORE</a></article>
  </section>
  <a class="directory" href="#">DIRECTORY SERVICES</a>
  <a class="social gallery" href="#" aria-label="Photo gallery"></a>
  <a class="social feed" href="#" aria-label="News feed"></a>
  <section class="quick">
    <h2>Quick links</h2>
    <ul>
      <li>Shop online</li><li>Scholarships</li><li>Strategic partners</li><li>PR grants</li>
      <li>Harbour Images</li><li>The Harbourline Foundation</li><li>Membership</li><li>Future Vision</li>
      <li>HarbourLINK</li><li>Harbour videos</li><li>HSA theme</li><li>Districts and zones</li>
    </ul>
  </section>
</main>
<footer>
  <ul class="footer-links">
    <li>Contact Us</li><li>Privacy Policy</li><li>Terms of use</li><li class="plain">Site Map</li>
  </ul>
  <div class="lang">
    <h4><svg width="24" height="24" viewBox="0 0 24 24"><circle cx="12" cy="12" r="11" fill="#fff"/><circle cx="12" cy="12" r="7" fill="none" stroke="#07078a" stroke-width="1.5"/><path d="M5 12h14M12 5v14" stroke="#07078a" stroke-width="1.5"/></svg>Select Language</h4>
    <ul>
      <li>Deutsch</li><li>한국어</li><li>English</li><li>Italiano</li><li>Español</li><li>Português</li><li>Français</li><li>Svenska</li><li>日本語</li>
    </ul>
  </div>
  <p class="copy">Copyright © 2012 the harbourline shipping association</p>
</footer>
</body>
</html>
```